One piece Trade show banner, 8' x 8' square

One piece banner for trade show
8' x 8' airborne geophysical company

Target Market(s)

Business

Industry/Entity Type

mineral exploration and science

Colors
0054AA
0677BA
7BADD7
CADEEF
E8F1F8
FFC000
F8CF3A
FAE287
FDF2CF
FEFAEE

Requirements
Must have
• Company logo (attached), slogan (Airborne Geophysics for Discovery). We are looking for a new banner, for a standard 8 x 8' square one-piece booth. I have attached some pictures, our logo, our old banner for reference, and two examples from unrelated companies from a tradeshow that we like. If its possible I'd like to change the color of the helicopter from green to dark grey. IE, keep the orange and white, just change green to dark grey. Looking for a simple, clean design with minimal text.
Nice to have
• I have attached examples of banners that we like (2xIMG), plus our old 3-piece banner r.
Should not have
• Green in the helicopter. Please change the color of the helicopter with green/orange/white to dark grey/orange/white. IE change the green to dark grey and leave the orange and white alone. I've attached lots of pictures but I don't expect them all to be used.

```html
<!DOCTYPE html>
<html lang="en">
<head>
<meta charset="utf-8">
<title>Summit AeroGeo – Airborne Trade Show Banner</title>
<link href="https://fonts.googleapis.com/css2?family=Poppins:wght@400;500;700;800;900&display=swap" rel="stylesheet">
<style>
  :root {
    --navy: #0b2f7a;
    --royal: #0054aa;
    --ocean: #0677ba;
    --sky: #7badd7;
    --mist: #cadeef;
    --ice: #e8f1f8;
    --gold: #ffc000;
    --sun: #f8cf3a;
    --white: #ffffff;
    --ink: #10204a;
    --stage: #e9ecf1;
  }
  * { box-sizing: border-box; margin: 0; padding: 0; }
  html, body { width: 1152px; height: 1200px; overflow: hidden; }
  body {
    background: var(--stage);
    font-family: "Poppins", sans-serif;
    position: relative;
  }
  .banner {
    position: absolute;
    left: 36px; top: 30px;
    width: 1080px; height: 1140px;
    overflow: hidden;
    background: linear-gradient(160deg, var(--royal) 0%, #0a5fb2 50%, #1a9ad6 100%);
  }
  .hero-photo {
    position: absolute;
    left: 0; top: 0; width: 1080px; height: 604px;
    background:
      linear-gradient(180deg, #0b2a78 0%, #1553a8 38%, #5f8fc4 58%, #b9cde0 66%, #7c7f72 78%, #5b5443 100%);
  }
  .brand {
    position: absolute;
    right: 64px; top: 78px;
    color: var(--white);
    font-weight: 500;
    font-size: 56px;
    line-height: 1;
    letter-spacing: -0.5px;
    display: flex; align-items: center; gap: 14px;
  }
  .brand-dot {
    width: 18px; height: 18px; border-radius: 50%;
    background: var(--white);
  }
  .headline {
    position: absolute;
    left: 0; width: 1080px; top: 405px;
    text-align: center;
    font-weight: 900;
    font-size: 172px;
    line-height: 1;
    letter-spacing: -4px;
    color: var(--white);
    text-shadow: 6px 6px 0 var(--ink);
  }
  .slogan-band {
    position: absolute;
    left: 0; top: 604px; width: 1080px; height: 104px;
    background: var(--white);
    display: flex; align-items: center; justify-content: center;
  }
  .slogan {
    font-weight: 800;
    font-size: 62px;
    letter-spacing: -1.5px;
    color: var(--navy);
    line-height: 1;
  }
  .survey-photo {
    position: absolute;
    left: 50px; top: 740px; width: 292px; height: 350px;
    border: 4px solid var(--gold);
    border-radius: 26px;
    background: linear-gradient(180deg, #0a3fb0 0%, #0b5ad6 45%, #0a3c8c 100%);
  }
  .services {
    position: absolute;
    left: 372px; top: 740px; width: 660px; height: 370px;
    border: 4px solid var(--gold);
    border-radius: 26px;
    background: #1a4594;
    overflow: hidden;
  }
  .service-grid {
    display: grid;
    grid-template-columns: 1fr 1fr;
    column-gap: 20px;
    padding: 22px 30px 0 34px;
  }
  .service { margin-bottom: 26px; }
  .service h3 {
    color: var(--gold);
    font-weight: 800;
    font-size: 24px;
    line-height: 1.15;
    letter-spacing: -0.3px;
  }
  .service ul { list-style: none; }
  .service li {
    color: var(--white);
    font-size: 22px;
    line-height: 1.2;
    padding-left: 14px;
    position: relative;
  }
  .service li::before {
    content: "•";
    position: absolute; left: 0;
  }
  .web-footer {
    position: absolute;
    left: 0; bottom: 0; width: 100%; height: 66px;
    background: var(--gold);
    display: flex; align-items: center; justify-content: center;
    color: var(--navy);
    font-weight: 800;
    font-size: 30px;
    letter-spacing: -0.3px;
  }
</style>
</head>
<body>
  <main class="banner">
    <div class="hero-photo" role="img" aria-label="Grey, orange and white survey helicopter carrying a long sensor boom, flying above cloud-covered mountain peaks against a deep blue sky"></div>

    <div class="brand"><span class="brand-dot"></span>Summit AeroGeo</div>

    <h1 class="headline">AIRBORNE</h1>

    <div class="slogan-band">
      <p class="slogan">GEOPHYSICS FOR DISCOVERY</p>
    </div>

    <div class="survey-photo" role="img" aria-label="Helicopter towing an electromagnetic survey loop beneath it against a deep blue sky"></div>

    <section class="services">
      <div class="service-grid">
        <div>
          <div class="service">
            <h3>ELECTROMAGNETICS</h3>
            <ul>
              <li>Frequency domain</li>
              <li>Time domain</li>
              <li>Passive</li>
            </ul>
          </div>
          <div class="service">
            <h3>RADIOMETRICS</h3>
            <ul>
              <li>256/512 channels</li>
              <li>Up to 42 litres</li>
            </ul>
          </div>
        </div>
        <div>
          <div class="service">
            <h3>MAGNETICS</h3>
            <ul>
              <li>Helicopter, fixed wing, and drone</li>
              <li>Total field &amp; gradient</li>
            </ul>
          </div>
          <div class="service">
            <h3>CONSULTING</h3>
            <ul>
              <li>Survey design</li>
              <li>Interpretations</li>
              <li>Inversions</li>
            </ul>
          </div>
        </div>
      </div>
      <div class="web-footer">WWW.SUMMITAEROGEO.COM</div>
    </section>
  </main>
</body>
</html>
```